Awesome business card design needed

We need a new business card design to go with our new logo.
We are a web development agency that specialises in highly complex back-end integrations as opposed to design, our customers are retailers, hotels, hospitals and any other organisation that has a large online marketing department.
Take a look at our website - www.brenoloft.com for some inspiration.
We want our new business cards to exude class, professionalism and style.
We are likely to choose a high-end card to print them on but we want the design of the card itself to really turn heads.
We have no specific colour requirements, the logo as you will see is a turquoise colour R89 G171 B167 #59aba7 but it can also be in white if you want to make the colour of the card something different.
The information on the card should be:
Name
Position
Tel
email
Potentially a double sided card could have our web address, twitter and FB links.

```html
<!DOCTYPE html>
<html lang="en">
<head>
<meta charset="utf-8">
<title>Brenoloft Business Card</title>
<link rel="stylesheet" href="https://fonts.googleapis.com/css2?family=Noto+Sans:wght@400;700&display=swap">
<style>
  :root {
    --teal: #59aba7;
    --ink: #2b2b2b;
    --sand: #e8d3ad;
    --card: #f6f2ea;
    --card-edge: #ddd5c6;
    --backdrop: #ebe6dc;
    --white: #ffffff;
  }
  html, body {
    margin: 0;
    padding: 0;
    width: 1200px;
    height: 1083px;
    overflow: hidden;
    background: var(--backdrop);
    font-family: "Noto Sans", Arial, sans-serif;
  }
  .canvas { position: relative; width: 1200px; height: 1083px; }
  .card {
    position: absolute;
    width: 601px;
    height: 343px;
    border-radius: 22px;
    overflow: hidden;
    background: var(--card);
    box-shadow: 0 0 0 1px var(--card-edge), 0 8px 22px rgba(0,0,0,0.10);
  }
  .card--front { left: 158px; top: 149px; }
  .card--back { left: 457px; top: 606px; }
  .card__band { position: absolute; left: 0; top: 0; width: 601px; height: 343px; }
  .wordmark {
    position: absolute;
    left: 0; right: 0;
    top: 44px;
    margin: 0;
    text-align: center;
    color: var(--teal);
    font-weight: 700;
    font-size: 80px;
    line-height: 1;
    letter-spacing: 2px;
  }
  .wordmark--reversed { transform: scaleX(-1); }
  .details {
    position: absolute;
    left: 0; right: 0;
    text-align: center;
    color: var(--white);
    margin: 0;
  }
  .details__name { top: 225px; font-size: 18px; }
  .details__name strong { font-weight: 700; font-size: 19px; }
  .details__line { font-size: 15.5px; line-height: 1; }
  .details__phone { top: 262px; }
  .details__web { top: 286px; }
  .details__address { top: 312px; font-size: 15px; letter-spacing: 0.3px; }
  .icon { display: inline-block; vertical-align: -2px; margin-right: 4px; }
  .follow {
    position: absolute;
    left: 0; right: 0;
    top: 248px;
    display: flex;
    justify-content: center;
    align-items: center;
    gap: 10px;
    color: var(--white);
    font-weight: 700;
    font-size: 19px;
  }
  .follow__square {
    width: 32px; height: 32px;
    border-radius: 6px;
    background: var(--white);
    opacity: 0.85;
  }
  .site {
    position: absolute;
    left: 0; right: 0;
    top: 300px;
    margin: 0;
    text-align: center;
    color: var(--white);
    font-size: 16px;
    letter-spacing: 2.5px;
  }
  .site strong { font-weight: 700; }
</style>
</head>
<body>
<main class="canvas">

  <section class="card card--front" aria-label="Card front">
    <svg class="card__band" viewBox="0 0 601 343" aria-hidden="true">
      <path d="M0,232 Q300,170 601,232 L601,343 L0,343 Z" fill="var(--ink)"/>
      <path d="M0,238 Q300,178 601,238 L601,343 L0,343 Z" fill="var(--sand)"/>
      <path d="M0,244 Q300,186 601,244 L601,343 L0,343 Z" fill="var(--teal)"/>
    </svg>
    <h1 class="wordmark">brenoloft</h1>
    <p class="details details__name"><strong>Your Name,</strong> Position</p>
    <p class="details details__line details__phone">
      <svg class="icon" width="13" height="13" viewBox="0 0 16 16" aria-hidden="true"><path d="M4 1 L6.5 4.5 L5 6.5 Q6.5 9.5 9.5 11 L11.5 9.5 L15 12 L13 15 Q6 14 1 3 Z" fill="none" stroke="#fff" stroke-width="1.4"/></svg>123-456-7890
    </p>
    <p class="details details__line details__web">
      <svg class="icon" width="13" height="11" viewBox="0 0 14 11" aria-hidden="true"><rect x="0.5" y="0.5" width="13" height="10" fill="#fff"/><path d="M0.5 0.5 L7 6 L13.5 0.5" fill="none" stroke="var(--teal)" stroke-width="1.2"/></svg>info@brenoloft.com
      <svg class="icon" width="12" height="12" viewBox="0 0 12 12" aria-hidden="true" style="margin-left:4px"><circle cx="6" cy="6" r="5.5" fill="#fff"/><circle cx="6" cy="6" r="2.5" fill="none" stroke="var(--teal)" stroke-width="1"/></svg>www.brenoloft.com
    </p>
    <p class="details details__line details__address">Street Name, City Name, State Zip Code</p>
  </section>

  <section class="card card--back" aria-label="Card back">
    <svg class="card__band" viewBox="0 0 601 343" aria-hidden="true">
      <path d="M0,232 Q300,170 601,232 L601,343 L0,343 Z" fill="var(--ink)"/>
      <path d="M0,238 Q300,178 601,238 L601,343 L0,343 Z" fill="var(--sand)"/>
      <path d="M0,244 Q300,186 601,244 L601,343 L0,343 Z" fill="var(--teal)"/>
    </svg>
    <p class="wordmark wordmark--reversed" aria-hidden="true">brenoloft</p>
    <div class="follow">
      <span>Follow Us On:</span>
      <span class="follow__square" aria-hidden="true"></span>
      <span class="follow__square" aria-hidden="true"></span>
    </div>
    <p class="site">www.<strong>brenoloft</strong>.com</p>
  </section>

</main>
</body>
</html>
```